VENTURE CAPITAL GROUP BUSINESS CARD DESIGN

Venture Capital Group based in SF looking for a bold business card design. No trendy colour explosion, 3D effects etc. Just "simple" optical effects. Works on your brain, keeps your eye focused and sticks to your mind.
Target Market(s)
Technology startups
Industry/Entity Type
Venture Capital
Contact Information for Business Card
DESMOND WHITLAKE
MANAGING PARTNER
187 FENWORTH ST SAN FRANCISCO, CA 94187
415.555.0142 O
415.555.0147 F
415.555.0193 C
desmond@veldtmoorcapital.ventures

```html
<!DOCTYPE html>
<html lang="en">
<head>
<meta charset="UTF-8">
<title>Veldtmoor Capital Group – Business Card</title>
<link href="https://fonts.googleapis.com/css2?family=Open+Sans:wght@400;600;700;800&display=swap" rel="stylesheet">
<style>
  :root {
    --backdrop: #2b2b2d;
    --card: #ffffff;
    --green-dark: #0f5a2a;
    --green-mid: #1e7d37;
    --green-light: #45b94b;
    --grey-panel: #c9cacc;
    --grey-disc: #d9dadb;
    --ink: #17532a;
  }
  * { margin: 0; padding: 0; box-sizing: border-box; }
  html, body { width: 1200px; height: 900px; overflow: hidden; }
  body {
    background: var(--backdrop);
    font-family: "Open Sans", Arial, sans-serif;
    position: relative;
  }
  .card {
    position: absolute;
    left: 250px;
    width: 700px;
    height: 400px;
    background: var(--card);
    border-radius: 26px;
    overflow: hidden;
  }
  .card--front { top: 35px; }
  .card--back { top: 465px; }

  .brand {
    display: flex;
    flex-direction: column;
    align-items: center;
    gap: 14px;
  }
  .brand__disc {
    border-radius: 50%;
    background: radial-gradient(circle at 40% 35%, #ffffff 0%, var(--grey-disc) 70%, #b9babc 100%);
  }
  .brand__name {
    color: var(--green-mid);
    font-weight: 600;
    letter-spacing: 0.08em;
    text-align: center;
    line-height: 1.25;
  }
  .card--front .brand {
    position: absolute;
    left: 0; right: 0; top: 95px;
  }
  .card--front .brand__disc { width: 120px; height: 120px; }
  .card--front .brand__name { font-size: 30px; }
  .card--front .brand__name small { display: block; font-size: 14px; letter-spacing: 0.35em; }

  .card--back .brand {
    position: absolute;
    right: 40px; top: 24px;
    gap: 8px;
  }
  .card--back .brand__disc { width: 64px; height: 64px; }
  .card--back .brand__name { font-size: 17px; }
  .card--back .brand__name small { display: block; font-size: 8px; letter-spacing: 0.35em; }

  .swoosh { position: absolute; inset: 0; }

  .person {
    position: absolute;
    left: 42px; top: 88px;
  }
  .person__name {
    color: var(--green-dark);
    font-weight: 800;
    font-size: 27px;
    letter-spacing: 0.02em;
    line-height: 1.3;
  }
  .person__title {
    color: var(--green-light);
    font-weight: 700;
    font-size: 15px;
    letter-spacing: 0.03em;
    line-height: 1.3;
  }

  .contact {
    position: absolute;
    left: 42px; top: 262px;
    color: var(--ink);
    font-weight: 600;
    font-size: 14px;
    line-height: 1.25;
  }
  .contact__address { margin-bottom: 5px; }
  .contact__row { display: flex; align-items: center; gap: 10px; }
  .contact__icon { width: 12px; height: 12px; fill: var(--ink); flex: none; }
</style>
</head>
<body>

<section class="card card--front">
  <div class="brand">
    <div class="brand__disc"></div>
    <div class="brand__name">VELDTMOOR<small>CAPITAL GROUP</small></div>
  </div>
</section>

<section class="card card--back">
  <svg class="swoosh" viewBox="0 0 700 400" preserveAspectRatio="none" aria-hidden="true">
    <defs>
      <linearGradient id="band-green" x1="0" y1="0" x2="1" y2="0">
        <stop offset="0" stop-color="#4cc04f"/>
        <stop offset="0.55" stop-color="#1e7d37"/>
        <stop offset="1" stop-color="#0f5a2a"/>
      </linearGradient>
    </defs>
    <path d="M0,250 C220,215 440,205 548,215 C600,230 592,300 552,400 L0,400 Z" fill="var(--grey-panel)"/>
    <path d="M0,190 C220,150 450,140 590,155 C665,168 650,300 600,400 L552,400 C592,300 600,230 548,215 C440,205 220,215 0,250 Z" fill="url(#band-green)"/>
  </svg>

  <div class="person">
    <div class="person__name">DESMOND WHITLAKE</div>
    <div class="person__title">MANAGING PARTNER</div>
  </div>

  <div class="brand">
    <div class="brand__disc"></div>
    <div class="brand__name">VELDTMOOR<small>CAPITAL GROUP</small></div>
  </div>

  <div class="contact">
    <div class="contact__address">187 FENWORTH ST SAN<br>FRANCISCO, CA 94187</div>
    <div class="contact__row">
      <svg class="contact__icon" viewBox="0 0 12 12" aria-label="Office"><path d="M2.5 0.5 L4.5 0.5 L5.3 3 L3.9 4.1 C4.6 5.6 6.2 7.3 7.9 8 L9 6.7 L11.5 7.5 L11.5 9.5 C11.5 10.6 10.6 11.5 9.5 11.5 C4.6 11.2 0.8 7.4 0.5 2.5 C0.5 1.4 1.4 0.5 2.5 0.5 Z"/></svg>
      <span>415.555.0142</span>
    </div>
    <div class="contact__row">
      <svg class="contact__icon" viewBox="0 0 12 12" aria-label="Fax"><rect x="3" y="0.5" width="6" height="3.5"/><rect x="0.5" y="4.5" width="11" height="5" rx="1"/><rect x="3" y="8.5" width="6" height="3"/></svg>
      <span>415.555.0147</span>
    </div>
    <div class="contact__row">
      <svg class="contact__icon" viewBox="0 0 12 12" aria-label="Mobile"><path d="M3.5 0.5 H8.5 A1 1 0 0 1 9.5 1.5 V10.5 A1 1 0 0 1 8.5 11.5 H3.5 A1 1 0 0 1 2.5 10.5 V1.5 A1 1 0 0 1 3.5 0.5 Z M3.7 1.8 V9 H8.3 V1.8 Z"/></svg>
      <span>415.555.0193</span>
    </div>
    <div class="contact__row">
      <svg class="contact__icon" viewBox="0 0 12 12" aria-label="Email"><path d="M0.5 2 H11.5 V10 H0.5 Z M1.5 3 V9 H10.5 V3 L6 6.5 Z M2.3 3 L6 5.8 L9.7 3 Z" fill-rule="evenodd"/></svg>
      <span>desmond@veldtmoorcapital.ventures</span>
    </div>
  </div>
</section>

</body>
</html>
```